Homecare Design. I would like the color to be same as my business cards

Gentle Hearth & Caregiver Agency
I would something very light on the eyes.
Easy to read nothing complicated
I want something that demonstrate soft touch
Updates

My contact number has change cell: 203-555-0187 office: 2035550142

Target Market(s)

Elderly
people looking for someone to take care of there love ones
Target age starting at 50

Industry/Entity Type

Business

Font styles to use
Serif

Colors
3176b5
3276b5
85acd3
ceddec

Requirements
Must have

Nice to have
• I woluld like something like helping hands
Should not have
• I really don't care to see medical supplies, medication

```html
<!DOCTYPE html>
<html lang="en">
<head>
<meta charset="utf-8">
<title>Gentle Hearth &amp; Caregiver Agency – Postcard</title>
<link rel="stylesheet" href="https://fonts.googleapis.com/css2?family=Roboto:wght@100;300;400&family=Tinos:ital,wght@1,700&family=Arimo:wght@400;700&display=swap">
<style>
  :root {
    --brand-blue: #3176b5;
    --brand-blue-alt: #3276b5;
    --mid-blue: #85acd3;
    --pale-blue: #ceddec;
    --deep-blue: #1f3f9a;
    --cyan: #5cc6ee;
    --page-bg: #1a1c1f;
    --card-white: #ffffff;
    --rule-grey: #8a8a8a;
    --stamp-grey: #6b6b6b;
  }
  * { margin: 0; padding: 0; box-sizing: border-box; }
  html, body { width: 920px; height: 1200px; overflow: hidden; }
  body { background: var(--page-bg); position: relative; font-family: "Arimo", Arial, sans-serif; }

  .card { position: absolute; background: var(--card-white); overflow: hidden; }
  .card--front { left: 88px; top: 23px; width: 730px; height: 565px; }
  .card--back { left: 90px; top: 611px; width: 724px; height: 560px; }

  /* Front */
  .hero-photo {
    position: absolute; left: 0; top: 0; width: 730px; height: 380px;
    background:
      radial-gradient(ellipse 190px 170px at 200px 150px, #e9d4c6 0%, #f1e6df 45%, rgba(255,255,255,0) 75%),
      linear-gradient(100deg, #e8edf2 0%, #f6f8fa 40%, #ffffff 70%, #f3f6f9 100%);
  }
  .front-wave { position: absolute; left: 0; top: 0; width: 730px; height: 565px; }
  .headline { position: absolute; right: 38px; text-align: right; color: var(--brand-blue); font-family: "Roboto", Arial, sans-serif; line-height: 1; white-space: nowrap; }
  .headline--caring { top: 80px; font-size: 70px; font-weight: 100; letter-spacing: 3px; color: #4f8bc6; }
  .headline--those { top: 152px; font-size: 48px; font-weight: 400; color: #3c7cbc; }
  .headline--matter { top: 220px; font-size: 84px; font-weight: 100; letter-spacing: 3px; color: #4f8bc6; }

  .front-info { position: absolute; left: 0; width: 730px; text-align: center; color: var(--card-white); white-space: nowrap; }
  .agency-name { font-family: "Tinos", "Times New Roman", serif; font-style: italic; font-weight: 700; }
  .front-info.agency-name { top: 389px; font-size: 29px; color: #f1f5fa; }
  .front-info--prompt { top: 439px; font-size: 18px; color: #e6eef7; }
  .front-info--phones { top: 464px; font-size: 27px; }
  .front-info--phones b { font-weight: 700; }
  .front-info--address { top: 503px; font-size: 16.5px; line-height: 21px; color: #e3ecf6; }

  /* Back */
  .back-title { position: absolute; left: 37px; top: 33px; font-size: 25px; color: var(--brand-blue); white-space: nowrap; }
  .intro { position: absolute; left: 38px; top: 82px; width: 290px; font-size: 13.4px; line-height: 17.2px; color: var(--brand-blue); text-align: justify; }
  .services-title { position: absolute; left: 40px; top: 189px; font-size: 15.5px; font-weight: 700; color: var(--brand-blue); }
  .service-list { position: absolute; left: 40px; top: 207px; list-style: none; font-size: 13.6px; line-height: 17.2px; color: var(--brand-blue); }
  .service-list li { display: flex; align-items: center; gap: 3px; white-space: nowrap; }
  .tick { width: 12px; height: 11px; flex: none; }
  .booking { position: absolute; left: 0; top: 395px; width: 350px; height: 68px; background: var(--brand-blue); color: var(--card-white); padding: 10px 0 0 39px; font-size: 15px; line-height: 17.5px; }
  .booking b { font-weight: 700; }

  .mail-address { position: absolute; left: 357px; top: 80px; width: 180px; text-align: center; font-size: 13.5px; line-height: 16.3px; color: var(--brand-blue); }
  .stamp-box { position: absolute; left: 580px; top: 43px; width: 96px; height: 108px; border: 1px solid #9a9a9a; padding: 26px 0 0 24px; font-family: "Roboto", Arial, sans-serif; font-weight: 300; font-size: 17.5px; line-height: 21px; color: var(--stamp-grey); }
  .address-rule { position: absolute; left: 385px; width: 297px; height: 0; border-top: 1px solid var(--rule-grey); }
</style>
</head>
<body>

<section class="card card--front">
  <div class="hero-photo" role="img" aria-label="Photo of a caregiver's hands gently holding an elderly person's hand on soft white bedding"></div>
  <svg class="front-wave" viewBox="0 0 730 565" aria-hidden="true">
    <path d="M0 322 C 230 318, 480 335, 730 338 L730 565 L0 565 Z" fill="var(--brand-blue)"/>
    <path d="M0 322 C 260 318, 520 345, 730 372 L730 378 C 520 356, 260 330, 0 330 Z" fill="var(--deep-blue)" opacity="0.7"/>
    <path d="M240 330 C 470 330, 640 318, 730 288 L730 300 C 640 330, 470 340, 240 332 Z" fill="var(--cyan)" opacity="0.9"/>
    <path d="M0 320 C 260 314, 520 328, 730 300 L730 306 C 520 334, 260 322, 0 326 Z" fill="var(--pale-blue)"/>
  </svg>
  <div class="headline headline--caring">CARING</div>
  <div class="headline headline--those">FOR THOSE THAT</div>
  <div class="headline headline--matter">MATTER</div>

  <div class="front-info agency-name">Gentle Hearth &amp; Caregiver Agency</div>
  <div class="front-info front-info--prompt">To schedule an appointment, please call:</div>
  <div class="front-info front-info--phones">Cell: <b>203-555-0187</b> Office: <b>2035550142</b></div>
  <div class="front-info front-info--address">Gentle Hearth and Caregiver Agency<br>48 LINDEN AVE NORWALK CT 06850 US</div>
</section>

<section class="card card--back">
  <h1 class="back-title agency-name">Gentle Hearth &amp; Caregiver Agency</h1>
  <p class="intro">Gentle Hearth &amp; Caregiver Agency, assist elderly clients who need assistance in or out of the home. Our home care services to our clients to assist them to lead dignified and independent lives in the comfort and safety of there own homes</p>

  <h2 class="services-title">Our Services</h2>
  <ul class="service-list">
    <li><svg class="tick" viewBox="0 0 12 11"><path d="M1 6 L4.5 9.5 L11 1" fill="none" stroke="var(--brand-blue)" stroke-width="2.2"/></svg>Assistance with Daily Living</li>
    <li><svg class="tick" viewBox="0 0 12 11"><path d="M1 6 L4.5 9.5 L11 1" fill="none" stroke="var(--brand-blue)" stroke-width="2.2"/></svg>Light cooking</li>
    <li><svg class="tick" viewBox="0 0 12 11"><path d="M1 6 L4.5 9.5 L11 1" fill="none" stroke="var(--brand-blue)" stroke-width="2.2"/></svg>Light Housekeeping</li>
    <li><svg class="tick" viewBox="0 0 12 11"><path d="M1 6 L4.5 9.5 L11 1" fill="none" stroke="var(--brand-blue)" stroke-width="2.2"/></svg>Running errands</li>
    <li><svg class="tick" viewBox="0 0 12 11"><path d="M1 6 L4.5 9.5 L11 1" fill="none" stroke="var(--brand-blue)" stroke-width="2.2"/></svg>Accompaniment to Doctors visits</li>
    <li><svg class="tick" viewBox="0 0 12 11"><path d="M1 6 L4.5 9.5 L11 1" fill="none" stroke="var(--brand-blue)" stroke-width="2.2"/></svg>Laundry</li>
    <li><svg class="tick" viewBox="0 0 12 11"><path d="M1 6 L4.5 9.5 L11 1" fill="none" stroke="var(--brand-blue)" stroke-width="2.2"/></svg>In and out home activities</li>
    <li><svg class="tick" viewBox="0 0 12 11"><path d="M1 6 L4.5 9.5 L11 1" fill="none" stroke="var(--brand-blue)" stroke-width="2.2"/></svg>Medication reminders</li>
    <li><svg class="tick" viewBox="0 0 12 11"><path d="M1 6 L4.5 9.5 L11 1" fill="none" stroke="var(--brand-blue)" stroke-width="2.2"/></svg>Hours of services range from 4 hrs to</li>
    <li><svg class="tick" viewBox="0 0 12 11"><path d="M1 6 L4.5 9.5 L11 1" fill="none" stroke="var(--brand-blue)" stroke-width="2.2"/></svg>Live-in services</li>
  </ul>

  <div class="booking">
    To schedule an appointment, please call:<br>
    Office - <b>203-555-0142)</b><br>
    <b>Cell - 203-555-0187</b>
  </div>

  <address class="mail-address" style="font-style:normal">Gentle Hearth<br>and Caregiver Agency<br>48 LINDEN AVE NORWALK<br>CT 06850 US</address>
  <div class="stamp-box">Place<br>Stamp<br>Here</div>
  <div class="address-rule" style="top:268px"></div>
  <div class="address-rule" style="top:327px"></div>
  <div class="address-rule" style="top:389px"></div>
</section>

</body>
</html>
```